MV Decor

There is a sample provided with the arabic text of the business card. please copy paste the same text and the same Logo (The two triangles) Just try to incorproate the Brown background attached (you are free to change the colors) Id like the colors to be mainly shades of black and red.

```html
<!DOCTYPE html>
<html lang="ar">
<head>
<meta charset="utf-8">
<title>MV Decor – Business Card</title>
<link href="https://fonts.googleapis.com/css2?family=Cairo:wght@400;500&family=Oswald:wght@600&family=Aref+Ruqaa:wght@400;700&display=swap" rel="stylesheet">
<style>
  :root {
    --backdrop: #5b3722;
    --card-red: #c8213f;
    --card-red-light: #d93a55;
    --card-red-deep: #a8182f;
    --ink-white: #f2f2f2;
    --ink-dark: #22231f;
    --card-shadow: rgba(0, 0, 0, 0.45);
  }
  * { margin: 0; padding: 0; box-sizing: border-box; }
  html, body {
    width: 1125px;
    height: 1200px;
    overflow: hidden;
    background: var(--backdrop);
  }
  .canvas {
    position: relative;
    width: 1125px;
    height: 1200px;
  }
  .card {
    position: absolute;
    left: 171px;
    width: 825px;
    height: 472px;
    overflow: hidden;
    box-shadow: 0 3px 8px var(--card-shadow);
    color: var(--ink-white);
  }
  .card--front { top: 106px; }
  .card--back { top: 639px; }
  .card__texture {
    position: absolute;
    inset: 0;
    background:
      radial-gradient(ellipse at 70% 30%, var(--card-red-light) 0%, transparent 60%),
      radial-gradient(ellipse at 20% 90%, var(--card-red-deep) 0%, transparent 55%),
      var(--card-red);
  }
  .brand-name {
    font-family: "Oswald", "Arial Narrow", sans-serif;
    font-weight: 600;
    color: var(--ink-white);
    letter-spacing: 3px;
    line-height: 1;
    white-space: nowrap;
  }
  .mark-square {
    display: block;
    background: var(--ink-dark);
    flex: none;
  }

  /* Front */
  .front__brand {
    position: absolute;
    left: 43px;
    top: 60px;
    font-size: 50px;
  }
  .front__person {
    position: absolute;
    right: 552px;
    top: 152px;
    text-align: right;
    direction: rtl;
    font-family: "Aref Ruqaa", serif;
    white-space: nowrap;
  }
  .person__name { font-size: 23px; line-height: 1.3; }
  .person__title { font-size: 15px; line-height: 1.3; padding-right: 30px; }
  .credentials {
    list-style: none;
    direction: rtl;
    text-align: right;
    font-family: "Cairo", sans-serif;
    font-weight: 500;
    white-space: nowrap;
  }
  .front__credentials {
    position: absolute;
    right: 552px;
    top: 244px;
    font-size: 19px;
    line-height: 27.5px;
  }
  .front__phone {
    position: absolute;
    left: 40px;
    top: 364px;
    display: flex;
    align-items: center;
    gap: 8px;
    font-family: "Cairo", sans-serif;
    font-size: 21px;
    font-weight: 500;
    white-space: nowrap;
  }
  .front__mark {
    position: absolute;
    left: 346px;
    top: 15px;
    width: 444px;
    height: 441px;
    display: flex;
    flex-direction: column;
    align-items: center;
    justify-content: center;
    gap: 30px;
  }
  .front__mark .mark-square { width: 160px; height: 160px; }
  .front__mark .brand-name { font-size: 64px; }

  /* Back */
  .back__mark-square {
    position: absolute;
    left: 180px;
    top: 150px;
    width: 130px;
    height: 130px;
  }
  .back__brand {
    position: absolute;
    left: 150px;
    top: 314px;
    width: 190px;
    text-align: center;
    font-size: 42px;
    letter-spacing: 2px;
  }
  .back__credentials {
    position: absolute;
    right: 123px;
    top: 104px;
    font-size: 23px;
    line-height: 33px;
  }
  .back__credentials li { position: relative; }
  .back__credentials li::before {
    content: "";
    position: absolute;
    left: -17px;
    top: 16px;
    width: 7px;
    height: 7px;
    border-radius: 50%;
    background: var(--ink-white);
  }
</style>
</head>
<body>
<main class="canvas">

  <section class="card card--front">
    <div class="card__texture" role="img" aria-label="Red background with a soft grid of small squares and circles"></div>
    <h1 class="brand-name front__brand">MV DECOR</h1>
    <div class="front__person">
      <p class="person__name">المهندس / سامر وليد المنصوري</p>
      <p class="person__title">أستاذ جامعي</p>
    </div>
    <ul class="credentials front__credentials">
      <li>ماجستير هندسة ديكور</li>
      <li>دبلوم عالي فن تشكيلي</li>
      <li>جامعة الفنون الجميلة (ليون)</li>
      <li>استشارات هندسية-فنية</li>
    </ul>
    <p class="front__phone">
      <svg width="18" height="18" viewBox="0 0 24 24" aria-hidden="true"><path fill="#f2f2f2" d="M6.6 10.8a15.1 15.1 0 0 0 6.6 6.6l2.2-2.2c.3-.3.7-.4 1-.2 1.1.4 2.3.6 3.6.6.6 0 1 .4 1 1V20c0 .6-.4 1-1 1C10.6 21 3 13.4 3 4c0-.6.4-1 1-1h3.5c.6 0 1 .4 1 1 0 1.3.2 2.5.6 3.6.1.3 0 .7-.2 1z"/></svg>
      <span>31245780 / 66120954</span>
    </p>
    <div class="front__mark">
      <span class="mark-square"></span>
      <span class="brand-name">MV DECOR</span>
    </div>
  </section>

  <section class="card card--back">
    <div class="card__texture" role="img" aria-label="Red background with a soft grid of small squares and circles"></div>
    <span class="mark-square back__mark-square"></span>
    <span class="brand-name back__brand">MV DECOR</span>
    <ul class="credentials back__credentials">
      <li>ماجستير هندسة ديكور</li>
      <li>دبلوم عالي فن تشكيلي</li>
      <li>جامعة الفنون الجميلة (ليون)</li>
      <li>استشارات هندسية-فنية</li>
      <li>ماجستير هندسة ديكور</li>
      <li>دبلوم عالي فن تشكيلي</li>
      <li>جامعة الفنون الجميلة (ليون)</li>
      <li>استشارات هندسية-فنية</li>
    </ul>
  </section>

</main>
</body>
</html>
```